Exclusive beauty salon needs a price list or services booklet

I need a new very attractive flyer for my beauty salon, containing information on the different services and their prices.
In attachment you can find a pdf of the "old" one, but I'd love to have a beautifully designed new one!
I'd love to have a booklet in format 148 x 148 mm, or in US format, containing 12 or 16 pages, but if you can offer other nice looking designs they are welcome!
The services that need to come in the booklet with their prices can all be found on my website: www.atelierverano.be, starting with
Gelaatsverzorging
Wimperverlenging
Suikerontharing
Wimperlifting
Permanente Make Up
Airbrush Tanning

Target Market(s)

woman from 20 to 89 years old

Industry/Entity Type

Beauty Salon

Font styles to use
Sans Serif

Colors

Designer to choose colors to be used in the design.

Requirements
Must have
• a classy nice look, it must contain details about the services from my beauty salon and their prices, and nice pictures.
• The Names, prices and explanations of the services can easily be found on my website: www.atelierverano.be
Nice to have
• In attachment you can find the "old" price list in pdf, what I need now is a "new booklet" with the new logo and updated services price list.
• I need a very nice and attractive looking booklet, classy chique, Paris chique, looking very expensive.
Should not have
• Not too much colors, not too curly, but still feminine

```html
<!DOCTYPE html>
<html lang="nl">
<head>
<meta charset="utf-8">
<title>Atelier Verano – Ontharing met suiker</title>
<link href="https://fonts.googleapis.com/css2?family=Open+Sans:ital,wght@0,300;0,400;1,300;1,400&display=swap" rel="stylesheet">
<style>
  :root{
    --backdrop:#b1d3d4;
    --paper:#f7f7f5;
    --teal:#4aa8ad;
    --ink:#7b7b7b;
    --ink-soft:#9a9a9a;
    --skin:#e2b89a;
    --skin-light:#f1ddd0;
  }
  *{margin:0;padding:0;box-sizing:border-box}
  html,body{width:1200px;height:700px;overflow:hidden}
  body{background:var(--backdrop);font-family:"Open Sans",sans-serif;color:var(--ink);position:relative}
  .spread{position:absolute;left:40px;top:140px;width:1120px;height:420px;display:flex;box-shadow:0 8px 24px rgba(0,0,0,.12)}
  .page{width:560px;height:420px;background:var(--paper);display:flex;overflow:hidden}
  .page--left{border-right:1px solid #e2e2df}
  .photo{height:100%;flex-shrink:0}
  .photo--leg{width:250px;background:linear-gradient(135deg,#f3ece7 0%,var(--skin-light) 45%,var(--skin) 75%,#f0eae6 100%)}
  .photo--jar{width:260px;background:linear-gradient(160deg,#f4eeee 0%,var(--skin-light) 50%,#e9d3c2 80%,#f2f0ee 100%)}
  .info{width:310px;padding:20px 18px 0 26px}
  .info__title{color:var(--teal);font-weight:400;font-size:13.5px;margin-bottom:8px}
  .info__intro{font-style:italic;font-weight:300;font-size:9px;line-height:1.28;margin-bottom:5px}
  .benefits{list-style:none;margin-top:9px}
  .benefits li{font-style:italic;font-weight:300;font-size:9px;line-height:1.22;padding-left:11px;position:relative;margin-bottom:5px}
  .benefits svg{position:absolute;left:0;top:3px;width:7px;height:6px}
  .prices{width:300px;padding:30px 30px 0 26px;display:flex;flex-direction:column}
  .prices__title{color:var(--teal);font-weight:400;font-size:13px;margin-bottom:10px}
  .price-list{list-style:none}
  .price-list li{display:flex;justify-content:space-between;align-items:baseline;font-style:italic;font-weight:300;font-size:11px;line-height:17.5px}
  .price-list small{font-size:8px}
  .price-list .amount{color:var(--teal);font-size:10px}
  .brand{margin-top:24px;display:flex;flex-direction:column;align-items:center;gap:8px}
  .brand__mark{width:9px;height:9px;border:1px solid var(--teal);border-radius:50%}
  .brand__name{color:var(--teal);font-weight:300;font-size:10px;letter-spacing:6px}
  .brand__web{font-weight:300;font-size:8px;letter-spacing:1px;color:var(--ink-soft)}
</style>
</head>
<body>
<main class="spread">
  <section class="page page--left">
    <div class="photo photo--leg" role="img" aria-label="Foto: suikerpasta wordt op een been aangebracht, rozenblaadjes op een handdoek"></div>
    <div class="info">
      <h1 class="info__title">Ontharing Met Suiker</h1>
      <p class="info__intro">Heb je ook genoeg van lichaams- en/of gezichtsbeharing maar ben je niet tevreden met het resultaat van scheren/harsen/laseren? Dan is ontharen met suiker van Dulcera dé oplossing!</p>
      <p class="info__intro">De voordelen van ontharen met suiker:</p>
      <ul class="benefits">
        <li><svg viewBox="0 0 7 6"><path d="M.5 3.2 2.6 5 6.5.6" fill="none" stroke="#4aa8ad" stroke-width="1.2"/></svg>De haren worden met de haargroeirichting verwijderd, hierdoor verminderd de pijn en je hebt geen last van haartjes die afbreken</li>
        <li><svg viewBox="0 0 7 6"><path d="M.5 3.2 2.6 5 6.5.6" fill="none" stroke="#4aa8ad" stroke-width="1.2"/></svg>De haren worden volledig verwijderd (met de haarwortel) waardoor ze dunner en donziger worden en minder snel aangroeien</li>
        <li><svg viewBox="0 0 7 6"><path d="M.5 3.2 2.6 5 6.5.6" fill="none" stroke="#4aa8ad" stroke-width="1.2"/></svg>Er wordt hygiënisch gewerkt</li>
        <li><svg viewBox="0 0 7 6"><path d="M.5 3.2 2.6 5 6.5.6" fill="none" stroke="#4aa8ad" stroke-width="1.2"/></svg>De huidstructuur verbetert door het verwijderen van dode huidcellen zonder de levende cellen te beschadigen</li>
        <li><svg viewBox="0 0 7 6"><path d="M.5 3.2 2.6 5 6.5.6" fill="none" stroke="#4aa8ad" stroke-width="1.2"/></svg>Suiker bestaat uit lichaamseigen stoffen waardoor de huid minder fel reageert op de ontharing.</li>
        <li><svg viewBox="0 0 7 6"><path d="M.5 3.2 2.6 5 6.5.6" fill="none" stroke="#4aa8ad" stroke-width="1.2"/></svg>Suikerontharing zorgt ervoor dat de haargroei vermindert na iedere behandeling en verfijnt de haarstructuur</li>
        <li><svg viewBox="0 0 7 6"><path d="M.5 3.2 2.6 5 6.5.6" fill="none" stroke="#4aa8ad" stroke-width="1.2"/></svg>Met suikerontharing werkt men op lichaamstemperatuur dus geen brandwonden</li>
        <li><svg viewBox="0 0 7 6"><path d="M.5 3.2 2.6 5 6.5.6" fill="none" stroke="#4aa8ad" stroke-width="1.2"/></svg>Suikerontharing is geschikt voor de couperose huid en is uiterst geschikt voor de meest gevoelige plaatsen (bikini, gezicht,...)</li>
        <li><svg viewBox="0 0 7 6"><path d="M.5 3.2 2.6 5 6.5.6" fill="none" stroke="#4aa8ad" stroke-width="1.2"/></svg>Suiker is wateroplosbaar, dus geen ongewenste plakseltjes</li>
      </ul>
    </div>
  </section>
  <section class="page page--right">
    <div class="prices">
      <h2 class="prices__title">TARIEVEN</h2>
      <ul class="price-list">
        <li><span>Wenkbrauwen</span><span class="amount">€9</span></li>
        <li><span>Wenkbrauwen en bovenlip</span><span class="amount">€16</span></li>
        <li><span>Bovenlip of kin</span><span class="amount">€9</span></li>
        <li><span>Bovenlip en kin</span><span class="amount">€16</span></li>
        <li><span>Gezicht <small>(bovenlip, kin, wangen en wenkbrauw)</small></span><span class="amount">€25</span></li>
        <li><span>Oksels</span><span class="amount">€12</span></li>
        <li><span>Armen</span><span class="amount">€20</span></li>
        <li><span>Brazilian bikini of string</span><span class="amount">€30</span></li>
        <li><span>Bikinilijn</span><span class="amount">€15</span></li>
        <li><span>Onderbeen en knie</span><span class="amount">€30</span></li>
        <li><span>Bovenbenen</span><span class="amount">€20</span></li>
        <li><span>Volledige benen (zonder bikini)</span><span class="amount">€50</span></li>
        <li><span>volledige benen incl. Bikinilijn</span><span class="amount">€59</span></li>
      </ul>
      <div class="brand">
        <span class="brand__mark"></span>
        <span class="brand__name">ATELIER VERANO</span>
        <span class="brand__web">www.atelierverano.be</span>
      </div>
    </div>
    <div class="photo photo--jar" role="img" aria-label="Foto: gehandschoende handen trekken suikerpasta uit een pot naast een been"></div>
  </section>
</main>
</body>
</html>
```